Restaurant Poster Design Project for A-Frame

I am after a poster, which will go on an outdoor A-Frame (A1 size - this size is to be confirmed) outlining our drink/happy hour/specials for our Mexican Restaurant and Bar.

Specific details are:

$4 Beer, Wine and Spirits
$5 Margaritas
everynight 5:30pm-7:30pm

I will supply logo, which needs to be incorporated (really small) into the poster, along with our address: 14 Marlow Lane, Windsor - (Im not too sure if we should include our phone number or not ?? Please advise what you feel will look good etc

Happy for you to add a phrase or wording etc, as long as the specific details are included, above.

We also have an enclosed beer garden in the rear of the restaurant - Do you believe I should mention this?

I am really open to eye catching designs and ALL suggestions welcome please!
Updates

Please find attached of samples that I am sort of after: (please let me know if they cant be opened).

http://www.flyerquill.example/blog/wp-content/uploads/2012/06/happyHourPoster-e1340372894746.gif

http://maxwelrue.files.samplepress.example/2012/10/profolio_0012.jpg?w=1169

http://3.bp.noteshelf.example/-NfNjpdG5w/T5pohPd0AhI/AAAAAAAADRs/CA7DPeI_PyU/s640/vintage_poster.jpg

http://www.quillharbors.example/files/imagecache/Event/news/teaser/Lounge_Happy_Hour_Poster_-_Mar_2011_bilingual.jpg

http://www.rtorvens.example/dallas/images/happyhour_poster.jpg

http://cdn2-b.lookoutpost.example/sites/default/files/styles/large_lightbox/hash/9a/d1/9ad11350ba178511886fddcff7aaac8d.jpg?itok=wDl2vlfJ

http://www.platecardfold.example/imageservice/images/13/1313171414293_244/img_large_watermarked.jpg

Target Market(s)

18 YEARS OLD AND OVER

Industry/Entity Type

Restaurant

Requirements
Must have
• Address
Phone Number
Logo
Clear easy to read font, to be seen via cars + ppl walking down street
If images are included, to be clear and visable
Nice to have
• Images are possible
To mention a beer garden
Should not have
• Traditional Mexican Colourful 80's Theme

```html
<!DOCTYPE html>
<html lang="en">
<head>
<meta charset="utf-8">
<title>Happy Hour – Casa Verano</title>
<link rel="stylesheet" href="https://fonts.googleapis.com/css2?family=Open+Sans:wght@700;800&family=Lobster+Two:ital,wght@1,700&display=swap">
<style>
  :root {
    --foam: #f7f4ec;
    --foam-shade: #d9cfb4;
    --beer-light: #f2cf4a;
    --beer-mid: #d9a21c;
    --beer-deep: #8a5a0c;
    --maroon: #8b1537;
    --earth: #2a1d0c;
    --ink: #1b1408;
    --garden-dark: #175238;
    --garden-grass: #4f7d1c;
    --garden-light: #86ab3a;
    --cream: #f3e6b2;
    --teal-edge: #0f4a45;
    --address: #e6f5ee;
  }
  * { margin: 0; padding: 0; box-sizing: border-box; }
  html, body { width: 848px; height: 1200px; overflow: hidden; background: var(--foam); }
  .poster {
    position: relative;
    width: 848px;
    height: 1200px;
    overflow: hidden;
    font-family: "Open Sans", Arial, sans-serif;
  }
  .backdrop { position: absolute; inset: 0; }
  .headline {
    position: absolute;
    top: 22px;
    left: 0;
    width: 848px;
    text-align: center;
    font-weight: 800;
    font-size: 128px;
    letter-spacing: -3px;
    line-height: 1;
    color: var(--beer-mid);
    background: linear-gradient(180deg, #f6da6a 0%, #e0a823 55%, #b9800f 100%);
    -webkit-background-clip: text;
    background-clip: text;
    -webkit-text-fill-color: transparent;
    filter: drop-shadow(4px 5px 2px rgba(40, 25, 5, 0.75));
  }
  .intro {
    position: absolute;
    top: 190px;
    left: 0;
    width: 848px;
    text-align: center;
    font-weight: 700;
    font-size: 29px;
    line-height: 1.5;
    color: var(--ink);
    text-shadow: 0 0 3px #fff, 3px 4px 4px rgba(0, 0, 0, 0.55);
  }
  .specials {
    position: absolute;
    top: 388px;
    left: 0;
    width: 848px;
    text-align: center;
    list-style: none;
    font-weight: 800;
    font-size: 53px;
    line-height: 76px;
    color: var(--maroon);
    text-shadow: 0 0 3px #fff6d6, 5px 6px 5px rgba(30, 15, 0, 0.7);
  }
  .garden {
    position: absolute;
    font-weight: 800;
    font-size: 70px;
    line-height: 1;
    filter: drop-shadow(5px 6px 3px rgba(30, 15, 0, 0.7));
  }
  .garden-beer { left: 122px; top: 740px; color: var(--garden-dark); }
  .garden-garden {
    left: 333px; top: 794px;
    background: linear-gradient(180deg, var(--garden-light), var(--garden-grass) 60%, #365a12);
    -webkit-background-clip: text;
    background-clip: text;
    -webkit-text-fill-color: transparent;
  }
  .brand {
    position: absolute;
    left: 40px;
    top: 1040px;
    display: flex;
    align-items: center;
    gap: 14px;
    font-weight: 800;
    font-size: 40px;
    color: var(--cream);
  }
  .brand-mark { width: 22px; height: 22px; background: var(--cream); }
  .address {
    position: absolute;
    right: 38px;
    top: 1126px;
    font-family: "Lobster Two", Georgia, cursive;
    font-style: italic;
    font-weight: 700;
    font-size: 40px;
    color: var(--address);
    -webkit-text-stroke: 1.2px var(--teal-edge);
    text-shadow: 3px 4px 3px rgba(0, 0, 0, 0.6);
  }
</style>
</head>
<body>
<main class="poster">
  <svg class="backdrop" width="848" height="1200" viewBox="0 0 848 1200" role="img" aria-label="Close-up photograph of a glass of golden beer with a foamy head and condensation droplets">
    <defs>
      <linearGradient id="beerFill" x1="0" y1="0" x2="0" y2="1">
        <stop offset="0" stop-color="#f7f3e8"/>
        <stop offset="0.24" stop-color="#efe8d2"/>
        <stop offset="0.3" stop-color="#e8c66a"/>
        <stop offset="0.34" stop-color="#f0c93f"/>
        <stop offset="0.7" stop-color="#dca524"/>
        <stop offset="1" stop-color="#c38a16"/>
      </linearGradient>
      <radialGradient id="vignette" cx="0.4" cy="0.55" r="0.7">
        <stop offset="0.55" stop-color="#000" stop-opacity="0"/>
        <stop offset="1" stop-color="#3a2204" stop-opacity="0.55"/>
      </radialGradient>
    </defs>
    <rect width="848" height="1200" fill="url(#beerFill)"/>
    <rect y="300" width="848" height="900" fill="url(#vignette)"/>
    <path d="M0 1022 C 260 1060, 560 1010, 848 888 L 848 1200 L 0 1200 Z" fill="var(--maroon)"/>
    <path d="M0 1034 C 260 1072, 560 1022, 848 900 L 848 1200 L 0 1200 Z" fill="var(--earth)"/>
  </svg>

  <h1 class="headline">happy hour</h1>
  <p class="intro">outlining our drink/happy hour/specials<br>for our Mexican Restaurant &amp; Bar.</p>

  <ul class="specials">
    <li>$4 Beer, Wine &amp; Spirits</li>
    <li>$5 Margaritas</li>
    <li>everynight</li>
    <li>5:30pm-7:30pm</li>
  </ul>

  <span class="garden garden-beer">Beer</span>
  <span class="garden garden-garden">Garden</span>

  <div class="brand"><span class="brand-mark"></span>Casa Verano</div>
  <p class="address">14 Marlow Lane, Windsor</p>
</main>
</body>
</html>
```